Stickers By Dwayne needs a website and logo design

I am starting a home business, "Stickers By Dwayne", which I will sell car decals/decals of some sort. I am looking for a creative and professional looking website. I do not want anything too plain/bland, or else I could design it myself. I am up for many options, when it comes to text/colors, and I am not opposed to much. Just nothing too plain. Currently have no logo design to use, may also add this to the project as well. ( I use Wordpress for my site server so it has to be compatible to be used with that website.
Also, I make decals that mainly go on car windows, not as big on car body’s. Also put decals on glassware, and other items. But mainly car windows

• some color, not be bland and white everywhere.

```html
<!DOCTYPE html>
<html lang="en">
<head>
<meta charset="utf-8">
<title>Stickers By Dwayne</title>
<link href="https://fonts.googleapis.com/css2?family=Montserrat:wght@400;500;600&family=Open+Sans:wght@400;600&display=swap" rel="stylesheet">
<style>
:root{
  --ink:#14151b;
  --navy:#0f1436;
  --footer:#0d0e1a;
  --bar:#06070c;
  --red:#d40f10;
  --sale-red:#e0512a;
  --white:#ffffff;
  --muted:#c9cbd6;
  --line:#e6e6e6;
  --text:#222;
}
*{margin:0;padding:0;box-sizing:border-box}
html,body{width:828px;height:1200px;overflow:hidden}
body{position:relative;background:var(--navy);font-family:'Montserrat',sans-serif;color:var(--white)}
.abs{position:absolute}
.site-header{left:0;top:0;width:828px;height:55px;background:var(--ink);z-index:2}
.brand{left:113px;top:20px;font-size:13.5px;font-weight:500;letter-spacing:.3px}
.nav a{position:absolute;top:23px;font-size:8px;color:var(--white);text-decoration:none}
.nav .active{left:354px;top:20px;width:39px;height:18px;background:var(--red);text-align:center;line-height:18px}
.hero-art{left:300px;top:20px;width:560px;height:360px;
  background:
    radial-gradient(ellipse 38% 42% at 60% 44%,rgba(196,24,44,.95) 0%,rgba(150,16,36,.85) 40%,rgba(60,14,40,.45) 75%,rgba(15,20,54,0) 100%),
    radial-gradient(ellipse 16% 30% at 52% 55%,rgba(10,10,16,.9) 0%,rgba(15,20,54,0) 100%);}
.hero-glow{left:0;top:55px;width:300px;height:280px;background:radial-gradient(ellipse 50% 55% at 35% 20%,rgba(150,160,205,.28),rgba(15,20,54,0) 100%)}
.hero-title{left:156px;top:160px;font-size:31px;font-weight:500;letter-spacing:.5px}
.shop-btn{left:202px;top:210px;width:102px;height:30px;background:var(--red);font-size:10.5px;text-align:center;line-height:30px;font-weight:500}
.dots{left:403px;top:293px}
.dots span{display:inline-block;width:5px;height:5px;border-radius:50%;background:#555a77;margin-right:4px}
.dots .on{background:none;border:1px solid #fff}
.feature h3{font-size:12.5px;font-weight:500;letter-spacing:.3px}
.feature p{font-family:'Open Sans',sans-serif;font-size:7px;line-height:9px;color:var(--muted);margin-top:7px;width:205px}
.feature .more{font-size:6.5px;margin-top:12px;letter-spacing:.3px}
.divider-v{left:414px;top:325px;width:1px;height:95px;background:#2a3055}
.panel{left:112px;top:443px;width:604px;height:566px;background:var(--white)}
.panel-title{left:112px;top:455px;width:604px;text-align:center;color:var(--text);font-size:17px;font-weight:500}
.card-img{width:129px;height:145px;border:1px solid var(--line)}
.sale{right:0;top:0;width:33px;height:15px;background:#000;font-size:5.5px;text-align:center;line-height:15px;color:#fff;font-weight:600}
.p-name{font-size:7.5px;color:var(--text);font-weight:500}
.p-price{font-size:7.5px;color:var(--text)}
.p-price s{margin-right:9px}
.p-price b{font-weight:400;color:var(--sale-red)}
.stars{font-size:6.5px;color:#333;letter-spacing:.5px}
.arrow-box{width:16px;height:16px;border:1px solid #ccc;background:#fff;color:#333;font-size:10px;text-align:center;line-height:14px}
.rule{left:112px;top:899px;width:604px;height:1px;background:#e2e2e2}
.partner{top:929px;width:52px;height:30px;border-radius:4px;background:#d6d6d6}
.chev{top:936px;color:#555;font-size:12px}
.site-footer{left:0;top:1022px;width:828px;height:161px;background:var(--footer)}
.foot-h{top:1045px;font-size:11px;font-weight:500;letter-spacing:.3px}
.foot-list{font-family:'Open Sans',sans-serif;font-size:7px;color:#e8e8ee;list-style:none}
.foot-list li{display:flex;align-items:flex-start}
.foot-list svg{flex:none;margin-right:8px}
.copyright{left:0;top:1183px;width:828px;height:17px;background:var(--bar);text-align:center;font-family:'Open Sans',sans-serif;font-size:6.5px;line-height:17px;color:#ddd}
</style>
</head>
<body>
<div class="abs hero-glow"></div>
<div class="abs hero-art" role="img" aria-label="Photo of a red car with white floral decals on its side, close up on the rear wheel"></div>

<header class="abs site-header">
  <div class="abs brand">STICKERS BY DWAYNE</div>
  <nav class="nav">
    <a class="active" href="#">Home</a>
    <a style="left:403px" href="#">About Us</a>
    <a style="left:456px" href="#">Car Decals</a>
    <a style="left:515px" href="#">FAQ</a>
    <a style="left:550px" href="#">Contact Us</a>
    <a style="left:609px" href="#"><svg width="8" height="7" viewBox="0 0 8 7"><path d="M0 0h1.5l1 4h4.5l1-3H2" fill="none" stroke="#fff"/><circle cx="3" cy="6" r=".8" fill="#fff"/><circle cx="6.5" cy="6" r=".8" fill="#fff"/></svg>&nbsp; Shopping Cart : item (0)</a>
  </nav>
</header>

<div class="abs hero-title">CAR DECALS</div>
<div class="abs shop-btn">SHOP NOW</div>
<div class="abs dots"><span></span><span class="on"></span><span></span></div>

<section class="abs feature" style="left:131px;top:336px">
  <svg class="abs" style="left:0;top:12px" width="28" height="26" viewBox="0 0 28 26"><path d="M2 10h6l14-8v20L8 14H2z" fill="#fff"/><path d="M7 15l3 9h3l-2-9z" fill="#fff"/></svg>
  <div style="margin-left:44px">
    <h3>PROMOTION</h3>
    <p>Habitasse molestie ullamcorper eu ipsum parturient risus at sagittis curae interdum consectetur mattis volutpat sed tincidunt sem torquent parturient eu.</p>
    <div class="more">READ MORE &#8853;</div>
  </div>
</section>
<div class="abs divider-v"></div>
<section class="abs feature" style="left:446px;top:336px">
  <svg class="abs" style="left:0;top:8px" width="28" height="26" viewBox="0 0 28 26"><rect x="5" y="1" width="22" height="24" fill="none" stroke="#fff" stroke-width="1.5"/><path d="M5 6H1v17a2 2 0 0 0 4 0" fill="none" stroke="#fff" stroke-width="1.5"/><rect x="9" y="5" width="7" height="6" fill="#fff"/><path d="M18 6h6M18 10h6M9 14h15M9 18h15M9 22h15" stroke="#fff" stroke-width="1.3"/></svg>
  <div style="margin-left:44px">
    <h3>NEWS &amp; UPDATES</h3>
    <p>Habitasse molestie ullamcorper eu ipsum parturient risus at sagittis curae interdum consectetur mattis volutpat sed tincidunt sem torquent parturient eu.</p>
    <div class="more">READ MORE &#8853;</div>
  </div>
</section>

<main class="abs panel"></main>
<h2 class="abs panel-title">Our Products</h2>

<div class="abs card-img" style="left:141px;top:493px;background:radial-gradient(ellipse 55% 35% at 50% 50%,#d7eed5 0%,#e6f3f2 45%,#fff 100%)" role="img" aria-label="Multicolour flame stripe decals"><div class="abs sale">SALE</div></div>
<div class="abs card-img" style="left:281px;top:493px;background:radial-gradient(ellipse 55% 35% at 50% 50%,#fbd9cc 0%,#fdeee8 45%,#fff 100%)" role="img" aria-label="Red and orange tribal flame decals"></div>
<div class="abs card-img" style="left:420px;top:493px;background:radial-gradient(ellipse 55% 25% at 50% 50%,#e6dcef 0%,#f4eef4 45%,#fff 100%)" role="img" aria-label="Running horse decal with flag pattern"><div class="abs sale">SALE</div></div>
<div class="abs card-img" style="left:560px;top:493px;background:radial-gradient(ellipse 55% 45% at 50% 50%,#f6dcb5 0%,#faece0 45%,#fff 100%)" role="img" aria-label="Car silhouettes showing side stripe decals"></div>

<div class="abs p-name" style="left:144px;top:648px">OMNIS VOLUPTAS</div>
<div class="abs p-name" style="left:283px;top:648px">OMNIS VOLUPTAS</div>
<div class="abs p-name" style="left:425px;top:648px">OMNIS VOLUPTAS</div>
<div class="abs p-name" style="left:566px;top:648px">OMNIS VOLUPTAS</div>
<div class="abs p-price" style="left:144px;top:663px"><s>$250</s><b>$150</b></div>
<div class="abs p-price" style="left:283px;top:663px"><s>$250</s><b>$150</b></div>
<div class="abs p-price" style="left:425px;top:663px"><s>$250</s><b>$150</b></div>
<div class="abs p-price" style="left:566px;top:663px"><s>$250</s><b>$150</b></div>
<div class="abs stars" style="left:230px;top:664px">★★★★★</div>
<div class="abs stars" style="left:370px;top:664px">★★★★☆</div>
<div class="abs stars" style="left:512px;top:664px">★★☆☆☆</div>
<div class="abs stars" style="left:653px;top:664px">★★★★★</div>

<div class="abs arrow-box" style="left:118px;top:668px">&lsaquo;</div>
<div class="abs arrow-box" style="left:694px;top:668px">&rsaquo;</div>

<div class="abs card-img" style="left:141px;top:685px;background:linear-gradient(180deg,#c8cdcb 0%,#a9b9bd 55%,#7f9aa6 100%)" role="img" aria-label="Photo of a blue toy car with grey flame decals"><div class="abs sale">SALE</div></div>
<div class="abs card-img" style="left:281px;top:685px;background:radial-gradient(ellipse 55% 40% at 50% 50%,#fbdccb 0%,#fdefe8 45%,#fff 100%)" role="img" aria-label="Orange, red and grey flame decals"></div>
<div class="abs card-img" style="left:420px;top:685px;background:linear-gradient(180deg,#15283d 0%,#102236 100%)" role="img" aria-label="Winged emblem artwork on dark navy"><div class="abs sale">SALE</div></div>
<div class="abs card-img" style="left:560px;top:685px;background:linear-gradient(180deg,#474747 0%,#3e3e3e 100%)" role="img" aria-label="Winged club emblem artwork on dark grey"></div>

<div class="abs p-name" style="left:144px;top:840px">OMNIS VOLUPTAS</div>
<div class="abs p-name" style="left:283px;top:840px">OMNIS VOLUPTAS</div>
<div class="abs p-name" style="left:425px;top:840px">OMNIS VOLUPTAS</div>
<div class="abs p-name" style="left:566px;top:840px">OMNIS VOLUPTAS</div>
<div class="abs p-price" style="left:144px;top:855px"><s>$250</s><b>$150</b></div>
<div class="abs p-price" style="left:283px;top:855px"><s>$250</s><b>$150</b></div>
<div class="abs p-price" style="left:425px;top:855px"><s>$250</s><b>$150</b></div>
<div class="abs p-price" style="left:566px;top:855px"><s>$250</s><b>$150</b></div>
<div class="abs stars" style="left:230px;top:856px">★★★★★</div>
<div class="abs stars" style="left:370px;top:856px">★★★★☆</div>
<div class="abs stars" style="left:512px;top:856px">★★☆☆☆</div>
<div class="abs stars" style="left:653px;top:856px">★★★★★</div>

<div class="abs rule"></div>
<div class="abs chev" style="left:126px">&lsaquo;</div>
<div class="abs partner" style="left:176px;width:40px;height:34px;top:927px"></div>
<div class="abs partner" style="left:266px;width:30px;height:34px;top:927px;border-radius:50%"></div>
<div class="abs partner" style="left:340px;width:56px;height:26px;top:931px"></div>
<div class="abs partner" style="left:424px;width:58px;height:24px;top:932px"></div>
<div class="abs partner" style="left:510px;width:62px;height:18px;top:935px"></div>
<div class="abs partner" style="left:604px;width:50px;height:28px;top:930px"></div>
<div class="abs chev" style="left:696px">&rsaquo;</div>

<footer class="abs site-footer"></footer>
<div class="abs foot-h" style="left:148px">CONTACT US</div>
<div class="abs foot-h" style="left:376px">INFORMATION</div>
<div class="abs foot-h" style="left:594px">SOCIAL MEDIA</div>

<ul class="abs foot-list" style="left:148px;top:1067px;line-height:12.5px">
  <li><svg width="8" height="10" viewBox="0 0 8 10"><path d="M4 10S0 5.5 0 4a4 4 0 0 1 8 0c0 1.5-4 6-4 6z" fill="#fff"/><circle cx="4" cy="4" r="1.5" fill="#0d0e1a"/></svg><span>Main Store 482 Harbor Lane<br>North Ridgeway</span></li>
  <li style="margin-top:10px"><svg width="9" height="9" viewBox="0 0 9 9"><path d="M1 0h2l1 2-1.2 1.2a6 6 0 0 0 3 3L7 5l2 1v2a1 1 0 0 1-1 1A8 8 0 0 1 0 1a1 1 0 0 1 1-1z" fill="#fff"/></svg><span>1-800 555-0142</span></li>
  <li style="margin-top:6px"><svg width="9" height="8" viewBox="0 0 9 8"><rect y="1" width="9" height="6" fill="#fff"/><path d="M0 1l4.5 3.5L9 1" fill="none" stroke="#0d0e1a"/></svg><span>hello@dwaynedecals.com</span></li>
  <li style="margin-top:8px"><svg width="10" height="10" viewBox="0 0 10 10"><circle cx="5" cy="5" r="4" fill="none" stroke="#fff" stroke-width="1.5"/><path d="M5 2.5V5h2" stroke="#fff" fill="none"/></svg><span>Morning - 9.00 am To 9.00 pm</span></li>
</ul>

<ul class="abs foot-list" style="left:377px;top:1066px;line-height:12.4px">
  <li><svg width="7" height="7" viewBox="0 0 7 7"><circle cx="3.5" cy="3.5" r="3.5" fill="#fff"/><path d="M2.8 2l1.5 1.5-1.5 1.5" stroke="#0d0e1a" fill="none"/></svg>Home</li>
  <li><svg width="7" height="7" viewBox="0 0 7 7"><circle cx="3.5" cy="3.5" r="3.5" fill="#fff"/><path d="M2.8 2l1.5 1.5-1.5 1.5" stroke="#0d0e1a" fill="none"/></svg>About Us</li>
  <li><svg width="7" height="7" viewBox="0 0 7 7"><circle cx="3.5" cy="3.5" r="3.5" fill="#fff"/><path d="M2.8 2l1.5 1.5-1.5 1.5" stroke="#0d0e1a" fill="none"/></svg>Car Decals</li>
  <li><svg width="7" height="7" viewBox="0 0 7 7"><circle cx="3.5" cy="3.5" r="3.5" fill="#fff"/><path d="M2.8 2l1.5 1.5-1.5 1.5" stroke="#0d0e1a" fill="none"/></svg>FAQ</li>
  <li><svg width="7" height="7" viewBox="0 0 7 7"><circle cx="3.5" cy="3.5" r="3.5" fill="#fff"/><path d="M2.8 2l1.5 1.5-1.5 1.5" stroke="#0d0e1a" fill="none"/></svg>Shopping Cart</li>
  <li><svg width="7" height="7" viewBox="0 0 7 7"><circle cx="3.5" cy="3.5" r="3.5" fill="#fff"/><path d="M2.8 2l1.5 1.5-1.5 1.5" stroke="#0d0e1a" fill="none"/></svg>Contact Us</li>
</ul>

<ul class="abs foot-list" style="left:595px;top:1071px;line-height:18.5px">
  <li style="align-items:center"><svg width="9" height="9" viewBox="0 0 9 9"><circle cx="4.5" cy="4.5" r="4" fill="#fff"/></svg>&nbsp;FRIENDPAGE</li>
  <li style="align-items:center"><svg width="9" height="9" viewBox="0 0 9 9"><rect x=".5" y=".5" width="8" height="8" fill="#fff"/></svg>&nbsp;SNAPGRID</li>
</ul>

<div class="abs copyright">All Rights Reserved. Copyrights @ 2017 company name</div>
</body>
</html>
```